Dashboard Elements

Hello – looking for someone to create dashboard elements.
I’ve already basically designed all these elements – but I need someone to take what I’ve designed and make it look like an actual dashboard UI, like an app - assuming using some kind of dashboard UI kit (but however you would like to get it done is fine). It can look just like mine or try something different, as long as it matches the color scheme webpage that I’m going to out it on – see the page here. I’m ok with making it dark, maybe that would look better – again as long as it matches the webpage (https://www.plandeck.io/file/7QxKtr2BwLpZnVe4Hs8Mc1/Webpage-with-placeholders?node-id=0%3A1). Please note, you do not need to put anything on the webpage or do anything with this Figma file, this is just a reference so you can color/stylize it accordingly.

The attached Powerpoint file has everything you need - make sure to zoom all the way out to see everything on the slides.

Here are the Dashboard elements needed (this will all make sense when you look at the PPT):
Dashboard 1
Dashboard 1 – expanded view A
Dashboard 1 – expanded view B
View Source button by itself
Source Document Viewer 1 and 2 (these are exactly the same just with a different image inside)*
Dashboard 2 (only slightly different than Dashboard 1, just extended with extra headings
Table of Contents
Searchbar and Source Doc by itself
*the documents in the source document viewers should still look like documents - they don’t need to look like part of the UI, because this is a document viewer – you can restyle/recolor if necessary or just leave these as is.
- Colors must match color scheme of webpage, attached and on Figma link (images there currently are only placeholders) – ok to go dark as long as it matches
- Must look sleek, clean, realistic
- Don’t add any pictures of people or change the text.
- In case it’s not clear, this is what I mean by the concept of Dashboard UI - https://www.notavia.net/shard/s7/sh/8fad21bc-14e9-4a7c-b2d0-5c3e9f71a604/92c4e1b7a05d3f68e1c2b947d0a3f815
- Must be sent in an editable file, I may need to be edit text and other elements
- If you are going to send a sample, please make sure it’s part of the dashboard itself, not just the table of contents etc

Ideally hoping to find someone I can continue working with as I'll have a lot more graphic design work needed coming up.

Thank you!

```html
<!DOCTYPE html>
<html lang="en">
<head>
<meta charset="utf-8">
<title>Glassmorphism – Compendium C-CDA</title>
<link href="https://fonts.googleapis.com/css2?family=Jost:wght@400&family=Rajdhani:wght@400;500&family=Roboto:ital,wght@0,300;0,400;0,500;0,700;1,400;1,500&display=swap" rel="stylesheet">
<style>
:root{
  --bg:#0e0b1c;
  --ink:#ffffff;
  --muted:#c9cbe0;
  --teal:#3fe0d0;
  --teal-2:#1a9fc0;
  --glass-top:#4a74a8;
  --glass-bot:#2c3f72;
  --purple:#3b2a8f;
  --purple-2:#5a3fc0;
  --grey-card:rgba(150,150,165,.42);
  --line:#5a5a8a;
}
*{box-sizing:border-box;margin:0;padding:0}
html,body{width:682px;height:1200px;overflow:hidden;background:var(--bg)}
body{position:relative;font-family:'Roboto',sans-serif;color:var(--ink)}
.abs{position:absolute}

.hero-band{left:0;top:0;width:682px;height:150px;background:var(--bg)}
.hero-title{left:51px;top:44px;font-family:'Jost',sans-serif;font-size:46px;letter-spacing:3px;font-weight:400}

.scene{left:0;top:150px;width:682px;height:1050px;overflow:hidden;
  background:
    radial-gradient(ellipse 120px 220px at 0px 230px,rgba(40,140,150,.55),transparent 70%),
    radial-gradient(ellipse 200px 260px at 700px 470px,rgba(60,130,140,.5),transparent 70%),
    radial-gradient(ellipse 160px 200px at 690px 10px,rgba(110,80,190,.55),transparent 70%),
    radial-gradient(ellipse 220px 160px at 60px 700px,rgba(40,110,110,.35),transparent 70%),
    radial-gradient(ellipse 200px 200px at 680px 1040px,rgba(90,60,170,.4),transparent 70%),
    var(--bg)}
.grid-line{position:absolute;top:0;width:1px;height:320px;background:rgba(255,255,255,.04)}

.section-label{left:50px;top:248px;font-family:'Rajdhani',sans-serif;font-size:11px;font-weight:500;letter-spacing:.8px}
.section-copy{left:50px;top:272px;width:230px;font-size:9.4px;font-weight:300;line-height:15.3px;color:var(--muted)}

.ccda-tag{left:402px;top:253px;width:52px;height:23px;border-radius:4px;background:linear-gradient(180deg,#1fa8c8,#1580a8);
  font-family:'Rajdhani',sans-serif;font-size:11px;letter-spacing:.6px;display:flex;align-items:center;justify-content:center}

/* Table of contents */
.toc-shadow{left:432px;top:176px;width:100px;height:222px;background:var(--purple);transform:skewX(-15deg);transform-origin:bottom left;border-radius:6px}
.toc{left:425px;top:168px;width:98px;height:220px;transform:skewX(-15deg);transform-origin:bottom left;border-radius:6px;
  background:linear-gradient(180deg,#6e9cc8,#3e5f93);border:1px solid rgba(255,255,255,.35)}
.toc-head{position:absolute;left:5px;top:6px;right:5px;height:17px;border-radius:3px;background:#e8eef8;display:flex;align-items:center;padding-left:4px;gap:4px}
.toc-head span{font-size:5.4px;color:#4b5bb5}
.toc-head .caret{margin-left:auto;margin-right:4px;width:0;height:0;border-left:3px solid transparent;border-right:3px solid transparent;border-bottom:4px solid #4b5bb5}
.toc-active{position:absolute;left:4px;top:31px;right:2px;height:19px;border:1px solid var(--teal);border-radius:2px;background:rgba(30,110,160,.5);display:flex;align-items:center;gap:4px;padding-left:4px}
.toc-active span{font-size:6.4px;color:#7fe8f0}
.toc-item{position:absolute;left:5px;display:flex;align-items:center;gap:5px;font-size:7.8px;font-weight:300}
.ico{width:10px;height:10px;border-radius:2px;background:linear-gradient(180deg,#6fe6f5,#2aa8d8);flex:none}
.ico.violet{background:linear-gradient(180deg,#8b7cf0,#4b5bd5)}

/* Insights panel */
.glass-panel{left:48px;top:469px;width:591px;height:335px;border-radius:8px;background:rgba(255,255,255,.035);border:1px solid rgba(255,255,255,.08)}
.insights-title{left:0;width:682px;top:508px;text-align:center;font-family:'Rajdhani',sans-serif;font-size:24px;font-weight:400;letter-spacing:2.4px;line-height:28px}
.insights-copy{left:140px;width:400px;top:577px;text-align:center;font-size:9.4px;font-weight:300;line-height:15.3px;color:var(--muted)}

/* HCC card */
.card-shadow{left:196px;top:669px;width:280px;height:203px;background:var(--purple);transform:skewX(-8.6deg);transform-origin:bottom left;border-radius:8px}
.hcc-card{left:187px;top:659px;width:276px;height:203px;transform:skewX(-8.6deg);transform-origin:bottom left;border-radius:8px;overflow:hidden;
  background:linear-gradient(180deg,var(--glass-top),var(--glass-bot));border:1px solid rgba(255,255,255,.45)}
.hcc-card .brand{position:absolute;left:14px;top:15px;display:flex;align-items:center;gap:3px;font-size:6px;letter-spacing:.3px}
.brand-dot{width:5px;height:5px;border-radius:50%;background:#9fd6ff}
.hcc-card .patient{position:absolute;right:10px;top:12px;font-size:3.6px;line-height:6px;color:#dfe6f5}
.hcc-card .card-title{position:absolute;left:0;right:0;top:27px;text-align:center;font-size:8.4px;color:#7fe8f0}
.hcc-card .summary{position:absolute;left:11px;top:46px;font-size:7.2px;color:#7fe8f0;display:flex;align-items:center;gap:3px}
.tri{width:0;height:0;border-left:2px solid transparent;border-right:2px solid transparent;border-top:3px solid currentColor}
.hcc-card .meta{position:absolute;right:8px;top:48px;font-size:4.6px;color:#fff}
.meta em{color:#7fe8f0;font-style:normal}
.thead{position:absolute;left:0;right:0;top:63px;height:16px;background:rgba(40,80,140,.6);font-size:4.6px;font-weight:700}
.trow{position:absolute;left:0;right:0;height:21px;border-bottom:1px solid rgba(255,255,255,.3);font-size:5.4px;font-weight:300}
.thead span,.trow span{position:absolute;top:50%;transform:translateY(-50%)}
.c-code{left:11px}.c-cond{left:57px}.c-cat{left:205px}.c-raf{left:237px}.c-arr{left:259px}
.trow .c-code,.trow .c-raf{color:#7fe8f0;font-weight:500}

.hover-ring{left:428px;top:803px;width:21px;height:21px;border-radius:50%;border:1px solid var(--teal);box-shadow:0 0 0 3px rgba(63,224,208,.25)}
.hover-badge{left:413px;top:834px;width:69px;height:14px;border-radius:2px;background:#3fcfbf;font-size:6.6px;font-weight:500;display:flex;align-items:center;justify-content:center;letter-spacing:.3px}

/* Expanded detail */
.detail-outer{left:193px;top:915px;width:300px;height:256px;border-radius:8px;background:var(--purple)}
.detail{left:202px;top:924px;width:282px;height:238px;border-radius:8px;border:1.5px solid rgba(255,255,255,.5);
  background:linear-gradient(180deg,#3b5f92,#2b4175)}
.d-text{position:absolute;font-size:5.6px;white-space:nowrap}
.d-teal{color:#7fe8f0;font-weight:500}
.d-bold{font-weight:700}
.view-btn{position:absolute;height:18px;border:1px solid var(--teal);border-radius:2px;display:flex;align-items:center;gap:4px;padding-left:7px;font-size:5.6px;background:rgba(20,60,90,.35)}
.doc-ico{width:5px;height:6px;border:.8px solid #fff;border-radius:1px}

.note-card{border-radius:3px;background:var(--grey-card);backdrop-filter:blur(2px);border:1px solid rgba(255,255,255,.18)}
.icon-circle{width:36px;height:36px;border-radius:50%;border:1px solid rgba(255,255,255,.25);background:rgba(40,40,80,.55);display:flex;align-items:center;justify-content:center}
</style>
</head>
<body>

<div class="abs hero-band"></div>
<h1 class="abs hero-title">GLASSMORPHISM</h1>

<div class="abs scene">
  <div class="grid-line" style="left:47px"></div>
  <div class="grid-line" style="left:100px"></div>
  <div class="grid-line" style="left:154px"></div>
  <div class="grid-line" style="left:208px"></div>
  <div class="grid-line" style="left:262px"></div>
  <div class="grid-line" style="left:316px"></div>
</div>

<svg class="abs" style="left:0;top:0" width="682" height="1200" viewBox="0 0 682 1200" aria-hidden="true">
  <g fill="none" stroke="var(--line)" stroke-width="1">
    <path d="M120 150 Q172 178 222 150"/>
    <path d="M266 150 C278 205 290 232 362 248"/>
    <circle cx="468" cy="279" r="108"/>
    <path d="M399 365 C350 380 338 410 338 469"/>
    <path d="M343 875 V915"/>
    <path d="M418 207 h30 v32 h-30 z" stroke="rgba(255,255,255,.18)"/>
    <path d="M418 209 v143 h20" stroke="rgba(255,255,255,.18)"/>
    <path d="M418 239 l20 -30" stroke="rgba(255,255,255,.18)"/>
  </g>
  <circle cx="362" cy="248" r="10" fill="#1aa0c8"/>
  <circle cx="399" cy="365" r="10" fill="#1aa0c8"/>
  <g stroke="var(--teal)" stroke-width="1.3">
    <path d="M99 1047 V1200"/>
    <path d="M588 1119 V1200"/>
  </g>
</svg>

<h2 class="abs section-label">COMPENDIUM C-CDA</h2>
<p class="abs section-copy">The normalized data is unified into the Compendium C-CDA. Enhanced composite longitudinal record in C-CDA format, the industry standard for all interoperability initiatives.</p>

<div class="abs ccda-tag">C-CDA</div>

<div class="abs toc-shadow"></div>
<nav class="abs toc" aria-label="Table of Contents">
  <div class="toc-head"><div class="ico violet" style="width:9px;height:9px"></div><span>Table of Contents</span><i class="caret"></i></div>
  <div class="toc-active"><div class="ico"></div><span>Insurance Provider</span></div>
  <div class="toc-item" style="top:54px"><i class="ico"></i>Problems</div>
  <div class="toc-item" style="top:70px"><i class="ico"></i>Results</div>
  <div class="toc-item" style="top:86px"><i class="ico"></i>Procedures</div>
  <div class="toc-item" style="top:102px"><i class="ico"></i>Encounters</div>
  <div class="toc-item" style="top:118px"><i class="ico"></i>Medications</div>
  <div class="toc-item" style="top:134px"><i class="ico"></i>Vital Signs</div>
  <div class="toc-item" style="top:151px"><i class="ico"></i>Immunizations</div>
  <div class="toc-item" style="top:168px"><i class="ico"></i>Social History</div>
  <div class="toc-item" style="top:185px"><i class="ico"></i>Family History</div>
  <div class="toc-item" style="top:201px"><i class="ico"></i>Plan of Care</div>
</nav>

<div class="abs glass-panel"></div>
<h2 class="abs insights-title">SUMMARIZED AND LINKED<br>TO KEY INSIGHTS</h2>
<p class="abs insights-copy">Insights are presented in a concise summary with direct links to supporting evidence. HCC opportunities are abstracted and cross-linked directly to the original text in the underlying record for quick and easy reference.</p>

<div class="abs card-shadow"></div>
<section class="abs hcc-card" aria-label="C-CDA Compendium HCC summary">
  <div class="brand"><i class="brand-dot"></i>MEDLATTICE</div>
  <div class="patient">Patient, MARY<br>| Female | 01/11/1951 &nbsp;| &nbsp;Age: 70</div>
  <div class="card-title">C-CDA Compendium</div>
  <div class="summary"><i class="tri" style="color:#fff"></i>HCC Summary</div>
  <div class="meta"><em>RAF: 1.462</em> | Condition Count: 5 | ID: 7326472</div>
  <div class="thead"><span class="c-code" style="color:#7fe8f0">ICC-10 Code</span><span class="c-cond">Condition</span><span class="c-cat">Category</span><span class="c-raf" style="color:#7fe8f0">RAF</span></div>
  <div class="trow" style="top:79px"><span class="c-code">J44.9</span><span class="c-cond">Chronic obstructive pulmonary disease</span><span class="c-cat">111</span><span class="c-raf">0.335</span><span class="c-arr"><i class="tri" style="color:#7fe8f0;display:block"></i></span></div>
  <div class="trow" style="top:100px"><span class="c-code">F33.1</span><span class="c-cond">Chronic kidney disease, moderate (stage 3)</span><span class="c-cat">138</span><span class="c-raf">0.069</span><span class="c-arr"><i class="tri" style="color:#7fe8f0;display:block"></i></span></div>
  <div class="trow" style="top:121px"><span class="c-code">F33.0</span><span class="c-cond">Major depressive disorder, recurrent, mild</span><span class="c-cat">59</span><span class="c-raf">0.309</span><span class="c-arr"><i class="tri" style="color:#7fe8f0;display:block"></i></span></div>
  <div class="trow" style="top:142px"><span class="c-code">I42.9</span><span class="c-cond">Cardiomyopathy</span><span class="c-cat">85</span><span class="c-raf">0.447</span><span class="c-arr"><i class="tri" style="color:#7fe8f0;display:block"></i></span></div>
  <div class="trow" style="top:163px"><span class="c-code">E11.36</span><span class="c-cond">Type 2 diabeters mellitus with diabetic cataract</span><span class="c-cat">18</span><span class="c-raf">0.302</span></div>
</section>

<div class="abs hover-ring"></div>
<svg class="abs" style="left:448px;top:822px" width="12" height="12" viewBox="0 0 12 12" aria-hidden="true"><path d="M1 1 L11 4 L6 6 L4 11 Z" fill="var(--teal)"/></svg>
<div class="abs hover-badge">Hover Animation</div>

<div class="abs detail-outer"></div>
<section class="abs detail" aria-label="E11.36 detail">
  <span class="d-text d-teal" style="left:11px;top:16px;font-weight:700">E11.36</span>
  <span class="d-text d-bold" style="left:41px;top:16px">Type 2 diabeters mellitus with diabetic cataract</span>
  <span class="d-text d-bold" style="left:197px;top:16px">18</span>
  <span class="d-text d-teal" style="left:237px;top:16px;font-weight:700">0.302</span>
  <i class="abs" style="left:256px;top:17px;width:0;height:0;border-left:2.5px solid transparent;border-right:2.5px solid transparent;border-bottom:3px solid #7fe8f0"></i>
  <span class="d-text" style="left:11px;top:32px;font-size:5px"><b>Why:</b> This patient was treated for cataracts that may be associated witj type 2 diabetes mellitus</span>

  <span class="d-text d-teal" style="left:15px;top:61px">Extracapsular Cataract with IOL</span>
  <span class="d-text d-bold" style="left:118px;top:61px">C-CDA: PROCEDURES</span>
  <div class="view-btn" style="left:217px;top:55px;width:56px"><i class="doc-ico"></i>View source</div>

  <span class="d-text d-teal" style="left:15px;top:133px">Diabetes Type 2</span>
  <span class="d-text d-bold" style="left:118px;top:133px">C-CDA: PROBLEM LIST</span>
  <div class="view-btn" style="left:217px;top:128px;width:56px"><i class="doc-ico"></i>View source</div>

  <span class="d-text d-teal" style="left:15px;top:206px">AntidiabeticDrug Class</span>
  <span class="d-text d-bold" style="left:118px;top:206px">C-CDA: PROBLEM LIST</span>
  <div class="view-btn" style="left:217px;top:200px;width:56px"><i class="doc-ico"></i>View source</div>
</section>

<div class="abs note-card" style="left:48px;top:1001px;width:288px;height:46px">
  <span class="d-text d-teal" style="left:14px;top:19px">Cataract</span>
  <span class="d-text d-teal" style="left:86px;top:9px;font-size:6.2px">Ophthalmology chart note</span>
  <span class="d-text" style="left:86px;top:20px;font-size:5.4px;line-height:8px;white-space:normal;width:90px">Patient presents for cataract evalution in the right eye.</span>
  <div class="view-btn" style="left:207px;top:12px;width:59px;height:19px"><i class="doc-ico"></i>View source</div>
</div>

<div class="abs note-card" style="left:352px;top:1073px;width:288px;height:46px">
  <span class="d-text d-teal" style="left:14px;top:19px">HbA1c</span>
  <span class="d-text d-teal" style="left:118px;top:8px;font-size:6.2px">Lab results</span>
  <span class="d-text" style="left:118px;top:16px;font-size:5.8px;line-height:7.6px">Hemoglobin A1C<br>6.9%<br>01/15/21</span>
  <div class="view-btn" style="left:207px;top:12px;width:59px;height:19px"><i class="doc-ico"></i>View source</div>
</div>

<div class="abs icon-circle" style="left:81px;top:1112px">
  <svg width="18" height="16" viewBox="0 0 18 16" fill="none" stroke="var(--teal)" stroke-width="1.1" aria-hidden="true">
    <rect x="1" y="5" width="4" height="10" rx="1"/><rect x="6" y="6" width="11" height="9" rx="1"/><rect x="8" y="1" width="7" height="5"/>
    <path d="M9 10h1M12 10h1M9 12.5h1M12 12.5h1"/>
  </svg>
</div>
<div class="abs icon-circle" style="left:570px;top:1149px">
  <svg width="18" height="18" viewBox="0 0 18 18" fill="none" stroke="var(--teal)" stroke-width="1.1" aria-hidden="true">
    <path d="M12 2 L16 6 M13 3 L4 12 a2 2 0 0 0 3 3 L15 5"/><path d="M7 9l2 2M9 7l2 2"/>
  </svg>
</div>

</body>
</html>
```